Business Card Design

I am a realtor and i also flip houses. I am CEO and Founder of my business which is Voskell Group LLC which is named after my great uncle who died and i was really close to. He was a wonderful friendly man so i want my business to represent him too. My business works with a lot of different people but i want mainly something to show i am a strong confidant woman who owns there own business. I have a really fun personality so i don't want anything TOO serious or manly. I want the perfect mix. My last two business cards i created are too embarrassing to hand out because they are far too girly and i deal with a lot of millionaire clients. I live out in the Palm Springs California area. I think its very important to show i am a single mom, female with her own business at only 24. I don't want to just be a female that blends in with all of the other serious people but yet i don't want to seem immature. People are telling me to stay away from pinks and purples but i don't want blues and greens because they represent men more. But i won't say no to them if there is a happy medium.

Industry/Entity Type

Realtor

Contact Information for Business Card

Voskell Group, LLC
Corinne Tabb
27358 Halvern Ave, C2 517
Cedar Hollow, ZQ 48613
760-419-6735
Corinnedtabb@mailvane.com

```html
<!DOCTYPE html>
<html lang="en">
<head>
<meta charset="utf-8">
<title>Voskell Group LLC — Business Card</title>
<link href="https://fonts.googleapis.com/css2?family=Electrolize&display=swap" rel="stylesheet">
<style>
  :root {
    --teal: #0097a0;
    --pink: #f99bcb;
    --mint: #a9e8b9;
    --ice: #c4eff0;
    --icon: #0b6f7a;
  }
  html, body {
    margin: 0;
    padding: 0;
    overflow: hidden;
    background: var(--teal);
  }
  .card {
    position: relative;
    width: 1200px;
    height: 702px;
    background: var(--teal);
    overflow: hidden;
    font-family: "Electrolize", "Share Tech", sans-serif;
  }
  .card__frame {
    position: absolute;
    inset: 0;
  }
  .card__line {
    position: absolute;
    left: 0;
    margin: 0;
    white-space: nowrap;
    line-height: 1;
    font-weight: 400;
  }
  .card__company {
    left: 376px;
    top: 118px;
    font-size: 46px;
    color: var(--mint);
    letter-spacing: 3.5px;
  }
  .card__name {
    left: 288px;
    top: 187px;
    font-size: 46px;
    color: var(--mint);
    letter-spacing: 4.5px;
  }
  .card__address,
  .card__contact {
    font-size: 33px;
    color: var(--ice);
    letter-spacing: 2.5px;
  }
  .card__address--street { left: 215px; top: 266px; }
  .card__address--suite  { left: 168px; top: 331px; }
  .card__address--city   { left: 224px; top: 401px; }
  .card__contact--phone  { left: 354px; top: 479px; letter-spacing: 2px; }
  .card__contact--email  { left: 431px; top: 546px; letter-spacing: 2px; }
  .card__icon {
    position: absolute;
  }
  .card__icon--phone { left: 296px; top: 478px; width: 42px; height: 42px; }
  .card__icon--email { left: 370px; top: 541px; width: 50px; height: 36px; }
</style>
</head>
<body>
<main class="card">
  <svg class="card__frame" viewBox="0 0 1200 702" width="1200" height="702" aria-hidden="true">
    <g fill="none" stroke="var(--pink)" stroke-width="20" stroke-linejoin="miter">
      <polyline points="0,343 113,343 376,80 1200,80"/>
      <polyline points="113,343 376,613 1200,613"/>
    </g>
    <g fill="var(--pink)">
      <rect x="933" y="130" width="267" height="28"/>
      <rect x="820" y="206" width="380" height="28"/>
      <rect x="688" y="267" width="512" height="28"/>
      <rect x="599" y="334" width="601" height="28"/>
      <rect x="686" y="404" width="514" height="28"/>
      <rect x="825" y="475" width="375" height="28"/>
      <rect x="931" y="539" width="269" height="28"/>
    </g>
  </svg>

  <h1 class="card__line card__company">Voskell Group LLC</h1>
  <p class="card__line card__name">Corinne Tabb</p>

  <p class="card__line card__address card__address--street">27358 Halvern Ave</p>
  <p class="card__line card__address card__address--suite">C2 517 Cedar Hollow</p>
  <p class="card__line card__address card__address--city">ZQ 48613</p>

  <svg class="card__icon card__icon--phone" viewBox="0 0 24 24" aria-hidden="true">
    <path fill="var(--icon)" d="M6.6 10.8c1.4 2.8 3.8 5.1 6.6 6.6l2.2-2.2c.3-.3.7-.4 1-.2 1.1.4 2.3.6 3.6.6.6 0 1 .4 1 1V20c0 .6-.4 1-1 1C10.6 21 3 13.4 3 4c0-.6.4-1 1-1h3.5c.6 0 1 .4 1 1 0 1.3.2 2.5.6 3.6.1.3 0 .7-.2 1z"/>
  </svg>
  <p class="card__line card__contact card__contact--phone">555-419-6735</p>

  <svg class="card__icon card__icon--email" viewBox="0 0 50 36" aria-hidden="true">
    <rect x="0" y="0" width="50" height="36" fill="var(--icon)"/>
    <polyline points="2,2 25,21 48,2" fill="none" stroke="var(--teal)" stroke-width="2.5"/>
    <line x1="2" y1="34" x2="19" y2="17" stroke="var(--teal)" stroke-width="2.5"/>
    <line x1="48" y1="34" x2="31" y2="17" stroke="var(--teal)" stroke-width="2.5"/>
  </svg>
  <p class="card__line card__contact card__contact--email">corinnedtabb@mailvane.com</p>
</main>
</body>
</html>
```